BOLD & MINIMALIST DESIGN NEEDED

We want a very bold but minimalistic business card design that is impactful and utilizes both sides of the business card. Our current logo is included for your use.

We want bold fonts and good use of negative space. We don't want the logo to overpower the design.

Target Market(s)

Professionals who are building new commercial buildings.

Industry/Entity Type

Construction

Contact Information for Business Card

Name, Title, email, office phone, cell phone, website

Font styles to use
Serif
Sans Serif

Requirements
Must have
• Bold design!

```html
<!DOCTYPE html>
<html lang="en">
<head>
<meta charset="UTF-8">
<title>Daniel Crane – Business Card</title>
<link href="https://fonts.googleapis.com/css2?family=Montserrat:wght@600;700;900&display=swap" rel="stylesheet">
<style>
  :root {
    --backdrop: #0b0b0b;
    --paper: #ffffff;
    --brand-green: #85c227;
    --ink: #111111;
    --rule: #1a1a1a;
  }
  * { margin: 0; padding: 0; box-sizing: border-box; }
  html, body {
    width: 1200px;
    height: 2228px;
    overflow: hidden;
    background: var(--backdrop);
    font-family: "Montserrat", Arial, sans-serif;
  }
  .canvas {
    position: relative;
    width: 1200px;
    height: 2228px;
  }
  .card {
    position: absolute;
    left: 202px;
    width: 789px;
    height: 454px;
    box-shadow: 0 4px 14px rgba(0, 0, 0, 0.5);
  }
  .card-front {
    top: 638px;
    background: var(--paper);
  }
  .card-front .name {
    position: absolute;
    left: 160px;
    top: 96px;
    font-weight: 900;
    font-size: 57px;
    letter-spacing: -0.5px;
    color: var(--brand-green);
    white-space: nowrap;
    line-height: 1;
  }
  .card-front .divider {
    position: absolute;
    left: 162px;
    top: 177px;
    width: 279px;
    height: 2px;
    background: var(--rule);
  }
  .card-front .title {
    position: absolute;
    left: 470px;
    top: 162px;
    font-weight: 700;
    font-size: 27px;
    letter-spacing: 0.5px;
    color: var(--ink);
    line-height: 1;
  }
  .card-front .contacts {
    position: absolute;
    left: 153px;
    top: 250px;
    list-style: none;
    font-weight: 600;
    font-size: 20px;
    color: var(--ink);
    line-height: 46px;
  }
  .card-front .accent-band {
    position: absolute;
    left: 0;
    bottom: 0;
    width: 100%;
    height: 26px;
    background: var(--brand-green);
  }
  .card-back {
    top: 1136px;
    background: var(--brand-green);
    display: flex;
    align-items: center;
    justify-content: center;
  }
  .brand {
    display: flex;
    align-items: center;
    gap: 16px;
    color: var(--paper);
    font-weight: 900;
    font-size: 34px;
    letter-spacing: 1px;
    white-space: nowrap;
  }
  .brand-mark {
    width: 26px;
    height: 26px;
    background: var(--paper);
  }
</style>
</head>
<body>
<main class="canvas">
  <section class="card card-front" aria-label="Card front">
    <h1 class="name">DANIEL CRANE</h1>
    <div class="divider"></div>
    <p class="title">ARCHITECT</p>
    <ul class="contacts">
      <li>555 014 2368</li>
      <li>info@danielcrane.com</li>
      <li>www.danielcrane.com</li>
    </ul>
    <div class="accent-band"></div>
  </section>

  <section class="card card-back" aria-label="Card back">
    <div class="brand">
      <span class="brand-mark"></span>
      <span class="brand-name">NORTHGATE DESIGN + BUILD</span>
    </div>
  </section>
</main>
</body>
</html>
```